Brochure Design - ICT Company

We are an ICT (Information & Communication Technologies) company and need a brochure design. Our main products and services are Office Equipment, Banking Equipment, Software Solutions, IT Hardware, Networking & Communication, Audio Video Solutions and Social Media Marketing. Please check our website www.zolvantek.com for details in our Solutions menu.

Designs should include colors from our website (blue) and our logo (orange/green) in the best possible combination with lighter colors. Graphics and patterns should be sleek and modern. Brochure size to be square shaped (21 cm x 21 cm).

Final design should portray us as a futuristic technology company.

Provide a design with sample images and we can purchase them if required. Alternatively, let us know if the images from our website will suffice.
Updates

Reason: Awaiting more designs and more creativity. If any input is required from us, do inform asap.

Uploaded 2 sample brochure designs that we found interesting - looking for more inspiring ideas.

Thanks

Hi everyone, the following text should appear on the cover of the brochure design:

'Your One Stop Solution Provider for Information & Communication Technologies'

Reason: Awaiting management feedback - might require changes in design. Open to receiving more designs.

Thank you all for participating. Received many creative ideas and will be back with more requests. 

Target Market(s)

Decision Makers in UAE: IT Managers, Purchase Manager, CEO, Finance Managers etc

Industry/Entity Type

Communication

Requirements
Must have
• We have 7 divisions within our company. Brochure should dedicate 2 pages to each company - Text on one side and Image on the other.

7 divisions are: (details on website)
Office Equipment - sales of copiers, fax etc to any industry, any size office
Banking Equipment - sales of coin counters, counterfeit detectors etc to banks and foreign exchange houses
IT & Communication - providing server, email, software licenses to any industry, any size office
Software Solution - Quillbase partner + provide software solution to any industry, any size company
ELV & Security - provide CCTV, security systems to big companies, warehouses etc any industry
AV & Convergence - provide latest technology multi sensory solutions for theatres, opera houses, education sector, hospitality sector, medical sector etc.
Social Media Marketing - provide marketing options to companies through social media (www.zolvanpost.com)

Images to be used in the brochure are attached - they are concept images associated with each division. The design for the inner pages can be created around this basic image.

Cover page - design with logo, 'An Information & Technologies Company'
Back page - Design with address details
Inner sections:
1. About Us
2. Seven divisions as described above

The pattern for the text for inner pages should be:
Heading describing problem
Small Paragraph text describing solution
Small inset images of the

Nice to have
• Modern, sleek look with images that reflect an ICT/IT company - stand out from the regular brochure design
Should not have
• The design should not use old-style design, fonts etc.

```html
<!DOCTYPE html>
<html lang="en">
<head>
<meta charset="utf-8">
<title>Zolvan Technologies – Brochure</title>
<link rel="stylesheet" href="https://fonts.googleapis.com/css2?family=Arimo:wght@400;700&display=swap">
<style>
:root{
  --stage:#8a8d90;
  --blue-deep:#2a2f86;
  --blue-mid:#2f54b0;
  --blue-light:#3f7fd0;
  --sky:#27a6df;
  --orange:#ec7a22;
  --green:#6cbf3a;
  --yellow:#f3dd2b;
  --fax-blue:#2ba4df;
  --pill-orange:#f09a34;
  --pill-green:#8fc83f;
  --teal:#2bb8b0;
  --ink:#1b1b1b;
  --grey-text:#555;
  --paper:#ffffff;
  --fold:#ececec;
}
*{box-sizing:border-box;margin:0;padding:0}
html,body{width:1200px;height:827px;overflow:hidden}
body{background:var(--stage);font-family:"Arimo",Arial,sans-serif;position:relative}

.cover{position:absolute;top:24px;width:360px;height:360px;overflow:hidden;color:#fff}
.back-cover{left:110px;background:linear-gradient(90deg,var(--blue-mid) 0%,var(--blue-deep) 100%)}
.front-cover{left:540px;background:linear-gradient(160deg,var(--blue-deep) 0%,var(--blue-mid) 55%,var(--blue-light) 100%)}

.brand{display:flex;align-items:flex-start;gap:5px;position:absolute}
.brand-mark{width:12px;height:12px;background:var(--orange);flex:none;margin-top:1px}
.brand-name{font-size:11px;line-height:11px;font-weight:400;letter-spacing:.3px}
.brand-tag{font-size:4px;line-height:5px;margin-top:3px;opacity:.9}

.back-cover .brand{left:170px;top:200px}
.contact-tab{position:absolute;left:12px;top:306px;background:#fff;color:var(--blue-deep);font-size:6px;padding:2px 4px}
.contact-row{position:absolute;left:12px;right:12px;top:318px;display:flex;justify-content:space-between;font-size:4.5px;line-height:6px;border-bottom:.6px solid rgba(255,255,255,.7);padding-bottom:4px}
.contact-row b{display:block;font-size:5px}
.back-cover .site{position:absolute;right:14px;bottom:14px;font-size:6px}

.front-cover .arcs{position:absolute;inset:0}
.front-cover .brand{right:16px;top:22px}
.front-cover .brand-name{font-size:10px;line-height:10px}
.tagline{position:absolute;left:80px;top:172px;font-size:11.5px}
.web-tag{position:absolute;left:262px;top:164px;background:#fff;color:var(--blue-deep);font-size:6.5px;font-weight:700;padding:2px 4px}
.divisions{position:absolute;left:8px;right:8px;bottom:10px;display:flex;justify-content:space-between;font-size:5px;opacity:.85}

.spread{position:absolute;left:250px;top:410px;width:920px;height:360px;background:var(--paper)}
.spread-fold{position:absolute;left:360px;top:0;width:20px;height:360px;background:linear-gradient(90deg,var(--paper),var(--fold),var(--paper))}
.spread-art{position:absolute;inset:0}
.about{position:absolute;left:14px;top:72px;width:150px}
.about h2{color:var(--sky);font-size:28px;font-weight:700;letter-spacing:-.5px;margin-bottom:8px}
.about p{font-size:5.6px;line-height:7.1px;color:var(--grey-text)}

.issue{position:absolute;font-weight:700;color:var(--ink);text-align:center;border-radius:14px;line-height:1}
.issue-copier{left:305px;top:64px;width:92px;height:36px;background:var(--yellow);font-size:14px;padding-top:4px}
.issue-fax{left:383px;top:122px;width:108px;height:42px;background:var(--fax-blue);font-size:14px;padding-top:6px}
.issue-std{left:212px;top:142px;width:145px;height:28px;background:var(--pill-orange);font-size:14px;padding-top:7px}
.issue-toner{left:346px;top:184px;width:146px;height:42px;background:var(--pill-green);font-size:14px;padding-top:6px}
.issue-admin{left:248px;top:230px;width:114px;height:56px;background:var(--teal);font-size:14px;padding-top:6px}

.system{position:absolute;font-size:7.5px;font-weight:700;color:var(--ink);letter-spacing:.3px}
.spread .brand{left:668px;top:14px;color:var(--blue-deep)}
.spread .brand-name{font-size:8px;line-height:8px}
.spread .brand-mark{width:9px;height:9px}
.office h3{position:absolute;left:604px;top:219px;color:var(--orange);font-size:14px;font-weight:700}
.office p{position:absolute;left:525px;top:245px;width:192px;height:92px;border:.8px dashed #999;font-size:5px;line-height:6.4px;font-weight:700;color:var(--ink);padding:6px 8px}
</style>
</head>
<body>

<section class="cover back-cover" aria-label="Back cover">
  <div class="brand">
    <span class="brand-mark"></span>
    <div><div class="brand-name">ZOLVAN<br>TECHNOLOGIES L.L.C.</div><div class="brand-tag">A Member of Zolvan Group<br>Your Partner in Growth</div></div>
  </div>
  <span class="contact-tab">Contact Us</span>
  <div class="contact-row">
    <div><b>Dubai &nbsp;UAE 204417</b>Tel : +971 4 555 0182 &nbsp;Fax : +971 4 555 0183</div>
    <div><b>Sharjah &nbsp;UAE 38120</b>Tel : +971 6 555 0241 &nbsp;Fax : +971 6 555 0242</div>
    <div><b>Abu Dhabi &nbsp;UAE 51906</b>Tel : +971 2 555 0317 &nbsp;Fax : +971 2 555 0318</div>
  </div>
  <span class="site">zolvantek.com</span>
</section>

<section class="cover front-cover" aria-label="Front cover">
  <svg class="arcs" viewBox="0 0 360 360" aria-hidden="true">
    <circle cx="290" cy="-60" r="190" fill="rgba(255,255,255,.07)"/>
    <circle cx="330" cy="-40" r="140" fill="rgba(255,255,255,.06)"/>
    <circle cx="170" cy="420" r="170" fill="rgba(255,255,255,.07)"/>
    <circle cx="300" cy="440" r="150" fill="rgba(255,255,255,.06)"/>
  </svg>
  <div class="brand">
    <span class="brand-mark"></span>
    <div><div class="brand-name">ZOLVAN<br>TECHNOLOGIES L.L.C.</div><div class="brand-tag">A Member of Zolvan Group<br>Your Partner in Growth</div></div>
  </div>
  <span class="web-tag">zolvantek.com</span>
  <p class="tagline">An Information &amp; Technologies Company</p>
  <div class="divisions">
    <span>▸Office Automation</span><span>▸Banking Equipment</span><span>▸IT &amp; Communications</span><span>▸Software Solutions</span><span>▸ELV &amp; Security</span><span>▸AV &amp; Convergence</span><span>▸Social Media</span>
  </div>
</section>

<section class="spread" aria-label="Inner spread: About Us and Office Systems">
  <div class="spread-fold"></div>
  <svg class="spread-art" viewBox="0 0 920 360">
    <g stroke="#aaa" stroke-width=".8" stroke-dasharray="4 3" fill="none">
      <line x1="170" y1="10" x2="170" y2="350"/>
      <line x1="8" y1="10" x2="8" y2="350"/>
      <circle cx="375" cy="178" r="168"/>
      <line x1="530" y1="10" x2="530" y2="235"/>
      <line x1="520" y1="135" x2="542" y2="58"/>
      <line x1="520" y1="135" x2="594" y2="80"/>
      <line x1="520" y1="135" x2="618" y2="104"/>
      <line x1="520" y1="135" x2="636" y2="128"/>
      <line x1="520" y1="135" x2="616" y2="154"/>
      <line x1="520" y1="135" x2="598" y2="179"/>
    </g>
    <circle cx="375" cy="178" r="132" fill="url(#paperBall)" role="img" aria-label="Illustration of a globe made of crumpled paper documents"/>
    <circle cx="520" cy="135" r="3" fill="#999"/>
    <defs>
      <radialGradient id="paperBall" cx="45%" cy="40%" r="60%">
        <stop offset="0" stop-color="#f2f2f2"/>
        <stop offset=".7" stop-color="#bdbdbd"/>
        <stop offset="1" stop-color="#8f8f8f"/>
      </radialGradient>
    </defs>
  </svg>

  <div class="about">
    <h2>About Us</h2>
    <p>Every business faces security challenges. It doesn't matter if you are the neighborhood grocery store, or the biggest bank in the world, you need security measures in place. Some companies may need security cameras to monitor things or access control systems to restrict access to certain areas. Other companies may need arm barriers, road blocks, or even tire killers to prevent traffic from going into high security areas. Every business needs a good smoke alarm and fire alarm system to ensure everyone's safety, and most all companies these days have some form of public address/speaker system and security alarm systems. What if there was a company your business was able to count on for all of these security needs?<br>There is a company you can count on, and it is Zolvan Technologies! We provide all of the services described above, and many, many more! Our goal is to make your company safe and secure! Whatever security challenges you may be facing, we are here to help! We have had over 15 years of experience in this industry, and our customers are always our number one priority! We are experts in the business security field and we can apply the highest technologies available to help your business! You can trust that when you choose us for your security needs, you are dealing with a top notch company whose goal is to serve you well, and make your company the best that it can be! If you think Zolvan Technologies would be a good fit to help your company with any security needs, feel free to reach out to us! We are always ready to help, and look forward to hearing from you! Just call us for a demo or visit our website at: http://www.zolvantek.com/ for more information!</p>
  </div>

  <div class="issue issue-copier">Copier<br>contracts</div>
  <div class="issue issue-fax">Fax service<br>agreements</div>
  <div class="issue issue-std">No standardization</div>
  <div class="issue issue-toner">Toner from<br>multiple suppliers</div>
  <div class="issue issue-admin">High<br>administration<br>costs</div>

  <div class="brand">
    <span class="brand-mark"></span>
    <div><div class="brand-name">ZOLVAN<br>TECHNOLOGIES L.L.C.</div></div>
  </div>

  <span class="system" style="left:543px;top:45px">Copy &nbsp;Systems</span>
  <span class="system" style="left:596px;top:67px">Print &nbsp;Systems</span>
  <span class="system" style="left:621px;top:92px">Large &nbsp;Format &nbsp;Systems</span>
  <span class="system" style="left:638px;top:117px">FAX &nbsp;Machines</span>
  <span class="system" style="left:619px;top:143px">Schredding &nbsp;Machines</span>
  <span class="system" style="left:601px;top:168px">Baling &nbsp;Machines</span>

  <div class="office">
    <h3>Office Systems</h3>
    <p>We are the prime distributors of office automation systems, based out from Dubai. Our custom made solution improves efficiency of your daily business process. Being able to do your daily schedules with minimized errors and more effectively means that you can lift your bottom line... Do more with less time and effort. This means significant cost savings and more time to focus on core business functions. Our award-winning range of color and monochrome products offers cost-effective, high-performance, high-value document management solutions for any office environment. Our multi-functional product range delivers a broad range of print/copy/scan/fax speeds up your business process to the maximum performance.</p>
  </div>
</section>

</body>
</html>
```